Cleaning service website design

We need a new nice web design(logo will be the same) for a new cleaning service Company:

Informations about Company and logo you can take from flyers in attachments.

This is a cleaning service Company which have simple rules and we would like to show that(in checklist form) on website:

- What we do and that we're Cleaning Green

- Why us?

- How much(our pricing is simple)

Also we would like to communicate with clients by some nice/big pictures on website and the most important thing is our phone number and short/fast Brimtallow.

Also there should be some space for description about our Company.

Generally all information on main page can be short: about us, about service(what we do), last reviews, tips (for example: Tip of the week) and other can be some introduction to subpage where will be more information.

There will be few subpages like: About us, About our service, Photos(Before and after), Reviews , Tips, FAQ, Contact, Looking for a Job? - most of them will be just text so you can project just one example.

```html
<!DOCTYPE html>
<html lang="en">
<head>
<meta charset="utf-8">
<title>Tidy Nest House Cleaning</title>
<link rel="stylesheet" href="https://fonts.googleapis.com/css2?family=PT+Sans:ital,wght@0,400;0,700;1,400&family=PT+Sans+Narrow:wght@700&display=swap">
<style>
:root{
  --green:#6cb31f;
  --green-dark:#4c8d12;
  --blue:#0d5da8;
  --ink:#222;
  --text:#3a3a3a;
  --muted:#999;
  --line:#cfcfcf;
  --orange:#f47a0c;
  --orange-light:#ffb300;
  --red:#e3141b;
}
*{box-sizing:border-box;margin:0;padding:0}
html,body{width:1200px;height:1039px;overflow:hidden;background:#fff;font-family:"PT Sans",sans-serif;color:var(--text)}
.page{position:relative;width:1200px;height:1039px}
.header{position:absolute;top:0;left:0;width:1200px;height:128px;background:#fff;border-bottom:6px solid #ececec}
.brand{position:absolute;left:150px;top:40px;display:flex;align-items:center;gap:10px}
.brand-dot{width:30px;height:30px;border-radius:50%;background:var(--green)}
.brand-name{font-size:28px;font-weight:700;color:var(--blue)}
.callout{position:absolute;right:150px;top:13px;text-align:right}
.callout-lead{font-size:14px;color:#333}
.callout-lead b{font-weight:700}
.callout-phone{display:flex;align-items:center;justify-content:flex-end;gap:6px;font-size:27px;font-weight:700;color:var(--ink);line-height:1.2}
.nav{position:absolute;right:150px;top:66px;display:flex;height:62px}
.nav a{display:block;padding:22px 16.5px 0;font-family:"PT Sans Narrow",sans-serif;font-weight:700;font-size:13.5px;color:#333;text-decoration:none;letter-spacing:.2px}
.nav a.active{background:#efefef;color:var(--green);border-bottom:6px solid var(--green);height:68px}
.hero{position:absolute;top:134px;left:0;width:1200px;height:502px;background:linear-gradient(100deg,#5f8a3a 0%,#b8552c 30%,#d47a4a 55%,#a74424 75%,#6f9a3d 100%)}
.hero-copy{position:absolute;left:150px;top:50px;color:#fff;text-shadow:0 1px 3px rgba(0,0,0,.45)}
.hero-title{font-size:42px;font-weight:400;letter-spacing:-.5px;line-height:1}
.hero-title b{font-weight:700}
.hero-sub{margin-top:14px;font-size:23px;font-weight:700}
.hero-sub .price{color:var(--red);font-size:40px;text-shadow:0 1px 2px rgba(0,0,0,.3)}
.perks{list-style:none;margin-top:10px}
.perks li{display:flex;align-items:center;gap:12px;height:33.6px;font-size:15.5px}
.leaf{width:20px;height:24px}
.badge{position:absolute;left:312px;top:275px;width:70px;height:70px;border-radius:50%;background:radial-gradient(circle at 50% 65%,#8fd13c,#e9f5dd 60%);border:3px solid #fff}
.cta{position:absolute;left:149px;top:376px;width:246px;height:57px;border-radius:4px;background:linear-gradient(#ffc300,var(--orange));display:flex;align-items:center;justify-content:center;gap:12px;color:#fff;font-size:27px;font-weight:700;text-shadow:0 1px 2px rgba(0,0,0,.3)}
.card{position:absolute;top:674px;width:288px;height:341px;border:1px solid var(--line);border-radius:3px;background:#fff;box-shadow:0 12px 10px -10px rgba(0,0,0,.2)}
.card-photo{margin:5px;height:108px}
.card h2{text-align:center;font-size:21px;font-weight:400;color:var(--green);margin-top:10px}
.checks{list-style:none;margin:14px 0 0 22px}
.checks li{display:flex;gap:9px;font-size:14px;line-height:19px;margin-bottom:9px;color:#333}
.checks svg{flex:none;margin-top:2px}
.prices{list-style:none;margin:14px 0 0 33px}
.prices li{font-size:14.5px;margin-bottom:7px;color:#333}
.prices b{font-weight:400;color:var(--green-dark)}
.note{margin:12px 0 0 37px;font-size:14px;line-height:17px;color:#333}
.note a{color:var(--blue)}
.fine{margin:14px 0 0 39px;font-size:11.5px;font-style:italic;color:#333}
.field{display:block;margin:0 0 13px 31px;width:225px;height:29px;border:1px solid #c8c8c8;padding:8px 12px;font-size:11px;color:var(--muted)}
.field-row{display:flex;gap:8px;margin-left:31px}
.field-row .field{margin:0;width:108px}
.form-foot{display:flex;justify-content:space-between;align-items:flex-end;margin:26px 31px 0 31px}
.form-call small{display:block;font-size:11px;font-weight:700;color:#111}
.form-call strong{font-size:19px;color:var(--blue)}
.submit{width:82px;height:27px;border-radius:2px;background:linear-gradient(#ff9a2a,#ee5f05);color:#fff;font-size:13px;font-weight:700;display:flex;align-items:center;justify-content:center;margin-bottom:4px}
</style>
</head>
<body>
<div class="page">
  <header class="header">
    <div class="brand"><span class="brand-dot"></span><span class="brand-name">Tidy Nest</span></div>
    <div class="callout">
      <p class="callout-lead"><b>Call Us</b> to arrange your cleaning on</p>
      <p class="callout-phone">
        <svg width="18" height="22" viewBox="0 0 18 22"><path d="M5 1 L8 6 L6 8 C7 12 9 15 12 17 L14 15 L17 19 L14 21 C7 19 2 11 2 4 Z" fill="var(--blue)"/></svg>
        555-014-2270
      </p>
    </div>
    <nav class="nav">
      <a class="active">HOME</a><a>ABOUT US</a><a>OUR SERVICES</a><a>PHOTOS</a><a>REVIEWS</a><a>TIPS</a><a>CAREERS</a><a>FAQ</a><a>CONTACT</a>
    </nav>
  </header>

  <section class="hero" role="img" aria-label="Photo of a smiling family of four outdoors in the sun">
    <div class="hero-copy">
      <h1 class="hero-title">SIMPLIFY <b>YOUR LIFE</b></h1>
      <p class="hero-sub">and some there House Cleaning from <span class="price">$79</span></p>
      <ul class="perks">
        <li><svg class="leaf" viewBox="0 0 20 24"><path d="M3 22 C1 12 8 3 19 1 C18 12 12 20 3 22 Z" fill="var(--green)"/></svg>Locally Owned &amp; Operated</li>
        <li><svg class="leaf" viewBox="0 0 20 24"><path d="M3 22 C1 12 8 3 19 1 C18 12 12 20 3 22 Z" fill="var(--green)"/></svg>Reliable &amp; Affordable</li>
        <li><svg class="leaf" viewBox="0 0 20 24"><path d="M3 22 C1 12 8 3 19 1 C18 12 12 20 3 22 Z" fill="var(--green)"/></svg>All Supplies Provided</li>
        <li><svg class="leaf" viewBox="0 0 20 24"><path d="M3 22 C1 12 8 3 19 1 C18 12 12 20 3 22 Z" fill="var(--green)"/></svg>No Contracts</li>
        <li><svg class="leaf" viewBox="0 0 20 24"><path d="M3 22 C1 12 8 3 19 1 C18 12 12 20 3 22 Z" fill="var(--green)"/></svg>Pet Friendly</li>
        <li><svg class="leaf" viewBox="0 0 20 24"><path d="M3 22 C1 12 8 3 19 1 C18 12 12 20 3 22 Z" fill="var(--green)"/></svg>Green Cleaning</li>
      </ul>
    </div>
    <div class="badge"></div>
    <div class="cta">GET STARTED
      <svg width="30" height="24" viewBox="0 0 30 24"><path d="M0 7 H15 V0 L30 12 L15 24 V17 H0 Z" fill="#fff"/></svg>
    </div>
  </section>

  <article class="card" style="left:148px">
    <div class="card-photo" role="img" aria-label="Photo of a family with a golden retriever on a sofa" style="background:linear-gradient(90deg,#c9a46f,#e8d7bd 50%,#9c8a74)"></div>
    <h2>What do we clean?</h2>
    <ul class="checks">
      <li><svg width="17" height="16" viewBox="0 0 17 16"><rect x="1" y="3" width="12" height="12" fill="none" stroke="var(--green-dark)" stroke-width="1.6"/><path d="M4 8 L7 12 L16 1" fill="none" stroke="var(--green-dark)" stroke-width="2.4"/></svg>Thoroughly clean your bathrooms, kitchen, bedrooms and living areas</li>
      <li><svg width="17" height="16" viewBox="0 0 17 16"><rect x="1" y="3" width="12" height="12" fill="none" stroke="var(--green-dark)" stroke-width="1.6"/><path d="M4 8 L7 12 L16 1" fill="none" stroke="var(--green-dark)" stroke-width="2.4"/></svg>Mop or vacuum your floors</li>
      <li><svg width="17" height="16" viewBox="0 0 17 16"><rect x="1" y="3" width="12" height="12" fill="none" stroke="var(--green-dark)" stroke-width="1.6"/><path d="M4 8 L7 12 L16 1" fill="none" stroke="var(--green-dark)" stroke-width="2.4"/></svg>Dust surfaces</li>
      <li><svg width="17" height="16" viewBox="0 0 17 16"><rect x="1" y="3" width="12" height="12" fill="none" stroke="var(--green-dark)" stroke-width="1.6"/><path d="M4 8 L7 12 L16 1" fill="none" stroke="var(--green-dark)" stroke-width="2.4"/></svg>Collect garbage</li>
      <li><svg width="17" height="16" viewBox="0 0 17 16"><rect x="1" y="3" width="12" height="12" fill="none" stroke="var(--green-dark)" stroke-width="1.6"/><path d="M4 8 L7 12 L16 1" fill="none" stroke="var(--green-dark)" stroke-width="2.4"/></svg>Make beds</li>
    </ul>
  </article>

  <article class="card" style="left:455px">
    <div class="card-photo" role="img" aria-label="Photo of a family looking at a laptop together" style="background:linear-gradient(90deg,#d9d2c4,#b9ad98 50%,#e6e4de)"></div>
    <h2>Pricing is..simple</h2>
    <ul class="prices">
      <li><b>$79</b> for homes less than 1000 sq ft</li>
      <li><b>$89</b> for homes 1000-1800 sq ft</li>
      <li><b>$99</b> for homes 1800-2600 sq ft</li>
    </ul>
    <p class="note">If your home is larger than 2600 sq ft please <a>call for a quote</a></p>
    <p class="fine">*rates are for regular service*</p>
  </article>

  <article class="card" style="left:762px">
    <h2 style="margin:18px 0 14px">Quick Free Estimate</h2>
    <div class="field">Name</div>
    <div class="field">E-mail</div>
    <div class="field">Postal Code</div>
    <div class="field">Phone</div>
    <div class="field-row"><div class="field">No. of Bathrooms</div><div class="field">No. of Bedrooms</div></div>
    <div class="form-foot">
      <div class="form-call"><small>CALL US TODAY</small><strong>555-014-2270</strong></div>
      <div class="submit">SUBMIT</div>
    </div>
  </article>
</div>
</body>
</html>
```